Dental clinic brochure design (Z fold)

We need a new brochure design made for our dental clinic - Corvellan Dental Surgery. One side is in English, the other is in Vietnamese - all text and translations provided in brochure sample with further instructions in word doc. We require a brochure design in a Z fold to convey a family friendly dental clinic, incorporating our logo colour into the theme and designers choice on complimentary colours. Additional high quality images are provided for use if required or free to use own images.

Colors
33b8a4
00a990
86cfc6

Requirements
Must have
• Easy to read font, flows from text to pictures and page to page
• At least 2 dental images

```html
<!DOCTYPE html>
<html lang="en">
<head>
<meta charset="utf-8">
<title>Corvellan Dental Surgery – Brochure Inside</title>
<link rel="stylesheet" href="https://fonts.googleapis.com/css2?family=Source+Sans+3:wght@400;600;700&display=swap">
<style>
  :root {
    --teal: #2bb9a9;
    --teal-deep: #00a990;
    --teal-soft: #86cfc6;
    --navy: #2e3192;
    --ink: #231f20;
    --paper: #ffffff;
  }
  * { margin: 0; padding: 0; box-sizing: border-box; }
  html, body { width: 1200px; height: 1000px; overflow: hidden; background: var(--paper); }
  body { font-family: "Source Sans 3", "Helvetica Neue", Arial, sans-serif; color: var(--ink); }
  .brochure { position: relative; width: 1200px; height: 1000px; }

  .side-band { position: absolute; left: 0; top: 73px; width: 208px; height: 855px; background: var(--teal); }

  .heading-pill {
    position: absolute; top: 128px; width: 316px; height: 108px;
    border: 4px solid var(--navy); border-radius: 56px; background: var(--paper);
    display: flex; align-items: center; padding-left: 34px;
    font-weight: 700; font-size: 27px; line-height: 34px; color: var(--ink);
    text-transform: uppercase;
  }
  .heading-pill--benefits { left: 55px; }
  .heading-pill--promos { left: 443px; border-color: var(--teal); color: var(--teal); padding-left: 46px; }
  .heading-pill--providers { left: 840px; padding-left: 46px; }

  .benefits-copy { position: absolute; left: 52px; top: 250px; width: 300px; font-size: 26px; line-height: 35px; }
  .benefits-copy p + p { margin-top: 22px; }
  .benefits-copy strong { font-weight: 700; }

  .photo { position: absolute; }
  .photo--children { left: 12px; top: 596px; width: 386px; height: 261px; background: linear-gradient(135deg, #f2d7b8, #e9c45a 45%, #f0a7b8 75%, #c9e06a); }
  .photo--smile { left: 405px; top: 544px; width: 392px; height: 261px; background: linear-gradient(120deg, #6f8ea0, #b89a7e 45%, #e7c1a8 70%, #8fa9b3); }

  .promo-copy { position: absolute; left: 437px; top: 252px; width: 340px; font-size: 23px; line-height: 30px; }
  .promo-copy p + p { margin-top: 14px; }
  .footnote { position: absolute; left: 437px; top: 824px; width: 320px; font-size: 16px; line-height: 22px; }

  .provider-list { position: absolute; left: 835px; top: 252px; width: 330px; list-style: none; font-size: 15.5px; line-height: 22px; }
  .provider-list li + li { margin-top: 4px; }

  .location-map { position: absolute; left: 838px; top: 435px; width: 205px; height: 235px; background: linear-gradient(160deg, #f4f4f4, #e6e6e6); }

  .contact-band { position: absolute; left: 797px; top: 697px; width: 403px; height: 231px; background: var(--teal); }
  .contact-label {
    position: absolute; left: 797px; top: 727px; width: 350px; height: 48px;
    background: var(--navy); border-radius: 0 24px 24px 0;
    color: #fff; font-weight: 700; font-size: 15.5px; letter-spacing: .2px;
    display: flex; align-items: center; padding-left: 29px;
  }
  .contact-card {
    position: absolute; left: 852px; top: 782px; width: 348px; height: 113px;
    background: var(--paper); border-radius: 48px 0 0 48px;
    padding: 14px 0 0 38px; font-size: 15px; line-height: 21px; font-style: normal;
  }
</style>
</head>
<body>
<main class="brochure">
  <div class="side-band"></div>

  <section class="panel panel--benefits">
    <h2 class="heading-pill heading-pill--benefits">Child Dental<br>Benefits Scheme</h2>
    <div class="benefits-copy">
      <p>A dental benefits program is available for eligible children aged 2 to 17 and will <strong>receive $1000</strong> for dental treatments.</p>
      <p>To check if your children are eligible call us on 9402 6185.</p>
    </div>
    <div class="photo photo--children" role="img" aria-label="Group of smiling children brushing their teeth"></div>
  </section>

  <section class="panel panel--promos">
    <h2 class="heading-pill heading-pill--promos">Special<br>Promotions</h2>
    <div class="promo-copy">
      <p>Gap free dental check-up, clean &amp; x-rays for all health insurances**</p>
      <p>At home whitening kit now $199 limited time only (normally $395).</p>
      <p>Braces, dentures and implants are available at our clinic.</p>
    </div>
    <div class="photo photo--smile" role="img" aria-label="Smiling girl with glasses wearing braces"></div>
    <p class="footnote">**Conditions apply—Ask staff for more information</p>
  </section>

  <section class="panel panel--providers">
    <h2 class="heading-pill heading-pill--providers">Dental<br>Providers</h2>
    <ul class="provider-list">
      <li>Dr Minh Tran BDSc (Melb), ICCDE</li>
      <li>Dr Quoc Vu BDSc (Melb), FICCDE<br>FRACDS, PGradDipCD Implants (Melb)</li>
      <li>Dr Lan Nguyen BHsc Mdent (Latrobe)</li>
      <li>Dr Anh Ho BHsc Mdent (Latrobe), FRACDS</li>
      <li>Dr Jade Lim BDS (Adl)</li>
    </ul>
    <div class="location-map" role="img" aria-label="Street map showing the clinic location"></div>

    <div class="contact-band"></div>
    <h3 class="contact-label">PRIMARY BUSINESS ADDRESS</h3>
    <address class="contact-card">
      48 Marlowe Road<br>
      Kestrel Vale, VIC 3094<br>
      Phone: (03) 9402 6185<br>
      Email: admin@corvellandental.com.au
    </address>
  </section>
</main>
</body>
</html>
```